Creation of brand identity and website "Tandem K"

I am currently seeking an brand, identity and web design for a new project called Tandem K. This is a brand new concept from scratch and you have free-reign on the whole design process, taking into account my preference below.

Must include the name "Tandem K", or "Tandem K: Or the year I woke Up". Kudos is this forms part of the brands logo

Design that can be easily scaled to potentially include: a blog, timeline and vlogs.

Minimal but effective use of colour (however any colours and combinations permitted

Use of icons/graphics over text wherever possible

Minimal use of frames and borders

I appreciate this is a fairly wide scope so please contact me on marblefinch@postwillow.com with any questions or more information on what the project is.

Target Market(s)

Male and Female 20-40
Blog readers
Selfhelp

Industry/Entity Type

Seeking

Number of Pages Required

1 page

Font styles to use
Serif
Sans Serif

Requirements
Must have
• It is in effect a blog design, so about me section, recent blog / archived posts, reader comments / Q and A section.
• A coded design would be appreciated to make my life easier however I have left the design as uncoded as getting the right design matters more to me and I want to keep the project open to as many designers as possible
Nice to have
• See project description for other details and please ask if you need anything else :)
Should not have
• Mustn't be cluttered or feel fussy
• Promote icons over text
• Frames / multiple borders

```html
<!DOCTYPE html>
<html lang="en">
<head>
<meta charset="utf-8">
<title>Tandem K: Or the Year I Woke Up</title>
<link href="https://fonts.googleapis.com/css2?family=Cinzel:wght@400;600&family=Lato:wght@300;400;700&family=PT+Sans:wght@700&display=swap" rel="stylesheet">
<style>
:root{
  --green:#7ba20f;
  --orange:#f8a21b;
  --ink:#3d3d3d;
  --body:#6a6a6a;
  --muted:#8c8c8c;
  --rule:#e2e2e2;
  --panel-head:#5c5c5c;
  --soft:#f2f2f2;
  --footer:#2a2a2a;
  --white:#ffffff;
}
*{box-sizing:border-box;margin:0;padding:0}
html,body{width:1200px;height:3114px;overflow:hidden}
body{position:relative;background:var(--white);font-family:"Lato",Arial,sans-serif;color:var(--body)}
.abs{position:absolute}

/* top bar */
.topbar{left:0;top:0;width:1200px;height:46px;background:var(--green)}
.topbar .social{position:absolute;right:24px;top:11px;display:flex;gap:12px}
.topbar .social span{width:22px;height:22px;border-radius:50%;background:var(--white);opacity:.9}

/* header */
.brand{left:0;top:70px;width:1200px;text-align:center;font-family:"Cinzel",Georgia,serif;font-weight:600;font-size:30px;color:var(--ink);letter-spacing:1px}
.nav{left:0;top:128px;width:1200px;display:flex;justify-content:center;align-items:center;font-family:"Lato",Arial,sans-serif;font-size:17px;letter-spacing:2.4px;color:var(--ink)}
.nav a{color:inherit;text-decoration:none;padding:0 26px;position:relative}
.nav a + a{border-left:1px solid #999}
.nav a.active{color:var(--green)}
.nav a.active::after{content:"";position:absolute;left:26px;right:26px;bottom:-21px;height:4px;background:var(--green)}

/* hero */
.hero{left:0;top:170px;width:1200px;height:397px;background:linear-gradient(180deg,#3b3a36 0%,#8a6a35 30%,#d49a3c 48%,#6a5a45 62%,#252220 100%)}
.hero .arrow{position:absolute;top:190px;width:22px;height:26px;background:#8d8d8d;display:flex;align-items:center;justify-content:center}
.hero .arrow.prev{left:0}
.hero .arrow.next{right:0}
.hero h1{position:absolute;left:0;right:0;top:272px;text-align:center;font-family:"PT Sans",Arial,sans-serif;font-weight:700;font-size:33px;line-height:42px;color:var(--white)}

/* categories */
.cats{left:0;top:567px;width:1200px;height:153px;display:flex}
.cat{flex:1;display:flex;align-items:center;padding-left:100px;gap:34px;background:var(--green);color:var(--white);font-family:"Cinzel",Georgia,serif;font-size:24px;letter-spacing:1.5px}
.cat.exercise{background:var(--orange);padding-left:84px}
.cat.sports{padding-left:50px}

/* posts */
.post{left:104px;width:654px}
.post h2{font-weight:400;font-size:23px;color:var(--ink);line-height:28px}
.post h3{font-weight:700;font-size:12.5px;color:var(--ink);margin-top:5px}
.post p{width:473px;font-size:12px;line-height:19.4px;margin-top:13px;color:var(--body)}
.post p a{color:var(--orange);font-style:italic;text-decoration:underline}
.post .thumb{position:absolute;right:2px;top:52px;width:142px;height:125px}
.post .meta{position:absolute;left:2px;top:194px;display:flex;font-size:11px;color:var(--muted)}
.post .meta span{display:flex;align-items:center;gap:7px}
.meta .date{width:125px}.meta .cmt{width:167px}.meta .like{width:104px}
.rule{left:104px;width:654px;height:1px;background:var(--rule)}

.comments{left:104px;top:998px;width:654px;height:192px;background:var(--soft);border:1px solid #d8d8d8}
.comments h4{position:absolute;left:14px;top:10px;font-size:13px;font-weight:700;color:var(--ink)}
.comments .c{position:absolute;left:14px;width:620px;display:flex;gap:40px;font-size:11.5px;line-height:17px}
.comments .c i{flex:none;width:34px;height:34px;border:2px solid var(--white)}
.comments .write{position:absolute;left:12px;top:150px;width:626px;height:30px;background:var(--white);border:1px solid #ddd;font-size:11px;font-style:italic;color:#aaa;padding:7px 10px}

.more{left:104px;top:2987px;width:654px;height:38px;background:#e6e6e6;display:flex;align-items:center;justify-content:center;gap:6px;font-size:12px;color:var(--ink)}

/* sidebar */
.side{left:793px;width:345px}
.side-head{height:42px;background:var(--panel-head);color:var(--white);display:flex;align-items:center;gap:10px;padding-left:18px;font-size:19px}
.search-box{height:74px;border:1px solid var(--rule);border-top:none;padding:19px 14px}
.search-box div{height:34px;border:1px solid #ddd;display:flex;align-items:center;justify-content:space-between;padding:0 10px;font-size:11px;color:#999}

.tabs{height:42px;display:flex;background:var(--panel-head)}
.tabs span{flex:1;display:flex;align-items:center;justify-content:center;gap:6px;color:var(--white);font-size:12px}
.tabs span.on{background:var(--white);color:var(--ink);border-left:1px solid var(--rule)}
.tabs i{width:16px;height:16px;border-radius:50%;border:2px solid currentColor}
.feed{height:303px;border:1px solid var(--rule);border-top:none;padding-top:15px}
.feed .item{display:flex;gap:10px;padding-left:10px;height:74px}
.feed .item i{flex:none;width:54px;height:54px}
.feed .item p{font-size:10.5px;line-height:15px;width:250px;color:var(--body)}
.feed .item b{display:inline-block;margin-top:6px;font-size:9.5px;font-weight:400;border:1px solid #c8cfe0;background:#eef1f7;color:#4a5a85;padding:1px 5px}

.archive{height:212px;border:1px solid var(--rule);border-top:none;padding:14px 18px}
.archive li{list-style:none;height:37px;border-bottom:1px solid #eee;display:flex;align-items:center;gap:14px;font-size:13px;color:var(--body)}
.archive li::before{content:"";width:4px;height:4px;border-radius:50%;background:var(--orange)}
.archive li:last-child{border-bottom:none}

.newsletter{height:166px;border:1px solid var(--rule);padding:14px 14px}
.newsletter h5{font-size:19px;font-weight:400;color:var(--ink)}
.newsletter p{font-size:11px;margin-top:6px}
.newsletter .field{margin-top:14px;width:310px;height:35px;border:1px solid #ddd;font-size:10.5px;font-style:italic;color:#aaa;padding:10px}
.newsletter .btn{margin-top:15px;width:94px;height:33px;background:var(--orange);color:var(--white);font-size:13px;font-weight:700;display:flex;align-items:center;justify-content:center;letter-spacing:1px}

.promo-a{left:793px;top:1771px;width:345px;height:257px;background:#8a8a8a}
.promo-b{left:793px;top:2064px;width:345px;height:199px;background:linear-gradient(135deg,#c7a378,#b98e5c 60%,#d0b08a)}

.footer{left:0;top:3068px;width:1200px;height:46px;background:var(--footer);color:#ddd;font-size:11.5px;display:flex;align-items:center;justify-content:center}

.ph1{background:linear-gradient(160deg,#7f8a92,#3c4754)}
.ph2{background:linear-gradient(160deg,#c9b8a2,#e7d8c4)}
.ph3{background:linear-gradient(160deg,#cbd8d6,#9aa9a6)}
.ph4{background:linear-gradient(160deg,#6e6e6e,#2d2d2d)}
.ph5{background:linear-gradient(160deg,#e8e8e6,#cfc7bb)}
.ph6{background:linear-gradient(160deg,#e4e4e4,#3b342e)}
.ph7{background:linear-gradient(160deg,#f4f4f4,#8e7563)}
</style>
</head>
<body>
<svg width="0" height="0" style="position:absolute">
  <symbol id="i-cal" viewBox="0 0 14 14"><rect x="1" y="2" width="12" height="11" rx="1" fill="#7ba20f"/><rect x="3" y="6" width="8" height="5" fill="#fff"/></symbol>
  <symbol id="i-cmt" viewBox="0 0 14 14"><path d="M7 1.5c3.6 0 6 2 6 4.5s-2.4 4.5-6 4.5l-4 2.5 1-3.2C2 8.8 1 7.5 1 6c0-2.5 2.4-4.5 6-4.5z" fill="#7ba20f"/></symbol>
  <symbol id="i-like" viewBox="0 0 14 14"><rect x="1" y="6" width="3" height="7" fill="#7ba20f"/><path d="M5 6l3-5c1 0 1.6.8 1.3 2L9 5.5h3.2c.8 0 1.2.7 1 1.4l-1.4 5.3c-.2.5-.6.8-1.1.8H5z" fill="#7ba20f"/></symbol>
  <symbol id="i-share" viewBox="0 0 14 14"><path d="M10.5 3L3.5 7l7 4" stroke="#7ba20f" stroke-width="1.5" fill="none"/><circle cx="10.5" cy="3" r="2.2" fill="#7ba20f"/><circle cx="3.5" cy="7" r="2.2" fill="#7ba20f"/><circle cx="10.5" cy="11" r="2.2" fill="#7ba20f"/></symbol>
</svg>

<div class="abs topbar"><div class="social" aria-label="Social links"><span></span><span></span><span></span><span></span></div></div>

<div class="abs brand">Tandem K: Or the Year I Woke Up</div>
<nav class="abs nav">
  <a class="active" href="#">ABOUT ME</a><a href="#">RECENT BLOG</a><a href="#">READER COMMENTS</a><a href="#">CONTACT US</a>
</nav>

<section class="abs hero" role="img" aria-label="Person with arms raised against a sunset over hills">
  <span class="arrow prev"><svg width="10" height="14" viewBox="0 0 10 14"><path d="M7 2L2 7l5 5" stroke="#fff" stroke-width="2" fill="none"/></svg></span>
  <span class="arrow next"><svg width="10" height="14" viewBox="0 0 10 14"><path d="M3 2l5 5-5 5" stroke="#fff" stroke-width="2" fill="none"/></svg></span>
  <h1>A Different Kind of Company<br>A Different Kind of Tandem K</h1>
</section>

<section class="abs cats">
  <div class="cat nutrition">
    <svg width="86" height="104" viewBox="0 0 86 104"><path d="M43 30c-10-8-38-8-40 22 0 26 18 48 30 48 5 0 7-3 10-3s5 3 10 3c12 0 30-22 30-48-2-30-30-30-40-22z" fill="#fff"/><path d="M44 30c0-10 3-18 10-24" stroke="#fff" stroke-width="5" fill="none"/><path d="M48 20c6-10 18-14 26-12-4 10-14 14-26 12z" fill="#fff"/></svg>
    NUTRITION
  </div>
  <div class="cat exercise">
    <svg width="100" height="100" viewBox="0 0 100 100"><circle cx="50" cy="16" r="12" fill="#fff"/><path d="M36 34h28l6 28 14 8-3 5-16-6-5-18v26H40V51l-5 18-16 6-3-5 14-8z" fill="#fff"/><path d="M8 90c14-12 30-16 42-16s28 4 42 16z" fill="#fff"/></svg>
    EXERCISE
  </div>
  <div class="cat sports">
    <svg width="120" height="104" viewBox="0 0 120 104"><circle cx="26" cy="78" r="20" stroke="#fff" stroke-width="6" fill="none"/><circle cx="94" cy="78" r="20" stroke="#fff" stroke-width="6" fill="none"/><circle cx="72" cy="12" r="10" fill="#fff"/><path d="M50 30l20 6 10 16h14" stroke="#fff" stroke-width="8" fill="none" stroke-linecap="round" stroke-linejoin="round"/><path d="M50 30L36 48l22 14v22" stroke="#fff" stroke-width="8" fill="none" stroke-linecap="round" stroke-linejoin="round"/></svg>
    SPORTS
  </div>
</section>

<!-- blog posts -->
<article class="abs post" style="top:772px">
  <h2>Lorem ipsum dolor sit</h2><h3>Duis aute irure dolor in reprehenderit</h3>
  <p>Lorem ipsum dolor sit amet, consecit adipiscing elit, sed do eiusmod tempor incidimen labore n dolorne laboris ni ut aliquip ex ena lin consequat Duis aute irure dolor in reprehenderit magna aliqua. Ut enim ad qnexercitation ullamco Neque porro quisquam est, qui dolorem ipsum quia dolor sit amet, conadipi velit sed quia non numquam eius modi tempora incidunt. ipsum quia dolor sit amet, conadipi velit sed quia non numquam eius modi tempora. <a href="#">Read More</a></p>
  <div class="thumb ph1" role="img" aria-label="Portrait of a man in a jacket"></div>
  <div class="meta"><span class="date"><svg width="13" height="13"><use href="#i-cal"/></svg>02/06/2016</span><span class="cmt"><svg width="13" height="13"><use href="#i-cmt"/></svg>Leave A Comment</span><span class="like"><svg width="13" height="13"><use href="#i-like"/></svg>Like Us</span><span><svg width="13" height="13"><use href="#i-share"/></svg>Share</span></div>
</article>
<section class="abs comments">
  <h4>Comments</h4>
  <div class="c" style="top:38px"><i class="ph2" role="img" aria-label="Reader avatar"></i><span>Lorem ipsum dolor sit amet, consecit adipiscing elit, sed do eiusmod tempor incidimen labore n dolorne laboris ni ut aliquip ex ena lin consequat Duis aute irure dolor in reprehenderit magna aliqua. Ut enim</span></div>
  <div class="c" style="top:98px"><i class="ph6" role="img" aria-label="Reader avatar"></i><span>Lorem ipsum dolor sit amet, consecit adipiscing elit, sed do eiusmod tempor incidimen labore n dolorne laboris ni ut aliquip ex ena lin consequat.</span></div>
  <div class="write">Write Comment</div>
</section>
<div class="abs rule" style="top:1212px"></div>

<article class="abs post" style="top:1256px">
  <h2>Lorem ipsum dolor sit</h2><h3>Duis aute irure dolor in reprehenderit</h3>
  <p>Lorem ipsum dolor sit amet, consecit adipiscing elit, sed do eiusmod tempor incidimen labore n dolorne laboris ni ut aliquip ex ena lin consequat Duis aute irure dolor in reprehenderit magna aliqua. Ut enim ad qnexercitation ullamco Neque porro quisquam est, qui dolorem ipsum quia dolor sit amet, conadipi velit sed quia non numquam eius modi tempora incidunt. ipsum quia dolor sit amet, conadipi velit sed quia non numquam eius modi tempora. <a href="#">Read More</a></p>
  <div class="thumb ph2" role="img" aria-label="Portrait of a blonde woman"></div>
  <div class="meta" style="top:200px"><span class="date"><svg width="13" height="13"><use href="#i-cal"/></svg>02/06/2016</span><span class="cmt"><svg width="13" height="13"><use href="#i-cmt"/></svg>Leave A Comment</span><span class="like"><svg width="13" height="13"><use href="#i-like"/></svg>Like Us</span><span><svg width="13" height="13"><use href="#i-share"/></svg>Share</span></div>
</article>
<div class="abs rule" style="top:1506px"></div>

<article class="abs post" style="top:1551px">
  <h2>Lorem ipsum dolor sit</h2><h3>Duis aute irure dolor in reprehenderit</h3>
  <p>Lorem ipsum dolor sit amet, consecit adipiscing elit, sed do eiusmod tempor incidimen labore n dolorne laboris ni ut aliquip ex ena lin consequat Duis aute irure dolor in reprehenderit magna aliqua. Ut enim ad qnexercitation ullamco Neque porro quisquam est, qui dolorem ipsum quia dolor sit amet, conadipi velit sed quia non numquam eius modi tempora incidunt. ipsum quia dolor sit amet, conadipi velit sed quia non numquam eius modi tempora. <a href="#">Read More</a></p>
  <div class="thumb ph3" role="img" aria-label="Portrait of a smiling man"></div>
  <div class="meta" style="top:200px"><span class="date"><svg width="13" height="13"><use href="#i-cal"/></svg>02/06/2016</span><span class="cmt"><svg width="13" height="13"><use href="#i-cmt"/></svg>Leave A Comment</span><span class="like"><svg width="13" height="13"><use href="#i-like"/></svg>Like Us</span><span><svg width="13" height="13"><use href="#i-share"/></svg>Share</span></div>
</article>
<div class="abs rule" style="top:1801px"></div>

<article class="abs post" style="top:1846px">
  <h2>Lorem ipsum dolor sit</h2><h3>Duis aute irure dolor in reprehenderit</h3>
  <p>Lorem ipsum dolor sit amet, consecit adipiscing elit, sed do eiusmod tempor incidimen labore n dolorne laboris ni ut aliquip ex ena lin consequat Duis aute irure dolor in reprehenderit magna aliqua. Ut enim ad qnexercitation ullamco Neque porro quisquam est, qui dolorem ipsum quia dolor sit amet, conadipi velit sed quia non numquam eius modi tempora incidunt. ipsum quia dolor sit amet, conadipi velit sed quia non numquam eius modi tempora. <a href="#">Read More</a></p>
  <div class="thumb ph4" role="img" aria-label="Black and white portrait of a man in a suit"></div>
  <div class="meta" style="top:208px"><span class="date"><svg width="13" height="13"><use href="#i-cal"/></svg>02/06/2016</span><span class="cmt"><svg width="13" height="13"><use href="#i-cmt"/></svg>Leave A Comment</span><span class="like"><svg width="13" height="13"><use href="#i-like"/></svg>Like Us</span><span><svg width="13" height="13"><use href="#i-share"/></svg>Share</span></div>
</article>
<div class="abs rule" style="top:2098px"></div>

<article class="abs post" style="top:2143px">
  <h2>Lorem ipsum dolor sit</h2><h3>Duis aute irure dolor in reprehenderit</h3>
  <p>Lorem ipsum dolor sit amet, consecit adipiscing elit, sed do eiusmod tempor incidimen labore n dolorne laboris ni ut aliquip ex ena lin consequat Duis aute irure dolor in reprehenderit magna aliqua. Ut enim ad qnexercitation ullamco Neque porro quisquam est, qui dolorem ipsum quia dolor sit amet, conadipi velit sed quia non numquam eius modi tempora incidunt. ipsum quia dolor sit amet, conadipi velit sed quia non numquam eius modi tempora. <a href="#">Read More</a></p>
  <div class="thumb ph5" role="img" aria-label="Portrait of a businesswoman"></div>
  <div class="meta" style="top:208px"><span class="date"><svg width="13" height="13"><use href="#i-cal"/></svg>02/06/2016</span><span class="cmt"><svg width="13" height="13"><use href="#i-cmt"/></svg>Leave A Comment</span><span class="like"><svg width="13" height="13"><use href="#i-like"/></svg>Like Us</span><span><svg width="13" height="13"><use href="#i-share"/></svg>Share</span></div>
</article>
<div class="abs rule" style="top:2393px"></div>

<article class="abs post" style="top:2437px">
  <h2>Lorem ipsum dolor sit</h2><h3>Duis aute irure dolor in reprehenderit</h3>
  <p>Lorem ipsum dolor sit amet, consecit adipiscing elit, sed do eiusmod tempor incidimen labore n dolorne laboris ni ut aliquip ex ena lin consequat Duis aute irure dolor in reprehenderit magna aliqua. Ut enim ad qnexercitation ullamco Neque porro quisquam est, qui dolorem ipsum quia dolor sit amet, conadipi velit sed quia non numquam eius modi tempora incidunt. ipsum quia dolor sit amet, conadipi velit sed quia non numquam eius modi tempora. <a href="#">Read More</a></p>
  <div class="thumb ph6" role="img" aria-label="Portrait of a woman with dark hair"></div>
  <div class="meta" style="top:203px"><span class="date"><svg width="13" height="13"><use href="#i-cal"/></svg>02/06/2016</span><span class="cmt"><svg width="13" height="13"><use href="#i-cmt"/></svg>Leave A Comment</span><span class="like"><svg width="13" height="13"><use href="#i-like"/></svg>Like Us</span><span><svg width="13" height="13"><use href="#i-share"/></svg>Share</span></div>
</article>
<div class="abs rule" style="top:2690px"></div>

<article class="abs post" style="top:2734px">
  <h2>Lorem ipsum dolor sit</h2><h3>Duis aute irure dolor in reprehenderit</h3>
  <p>Lorem ipsum dolor sit amet, consecit adipiscing elit, sed do eiusmod tempor incidimen labore n dolorne laboris ni ut aliquip ex ena lin consequat Duis aute irure dolor in reprehenderit magna aliqua. Ut enim ad qnexercitation ullamco Neque porro quisquam est, qui dolorem ipsum quia dolor sit amet, conadipi velit sed quia non numquam eius modi tempora incidunt. ipsum quia dolor sit amet, conadipi velit sed quia non numquam eius modi tempora. <a href="#">Read More</a></p>
  <div class="thumb ph7" role="img" aria-label="Portrait of a young man"></div>
  <div class="meta" style="top:203px"><span class="date"><svg width="13" height="13"><use href="#i-cal"/></svg>02/06/2016</span><span class="cmt"><svg width="13" height="13"><use href="#i-cmt"/></svg>Leave A Comment</span><span class="like"><svg width="13" height="13"><use href="#i-like"/></svg>Like Us</span><span><svg width="13" height="13"><use href="#i-share"/></svg>Share</span></div>
</article>

<div class="abs more"><svg width="14" height="14" viewBox="0 0 14 14"><circle cx="7" cy="7" r="6" fill="#999"/><circle cx="7" cy="7" r="2.5" fill="#e6e6e6"/></svg>Load More Blog</div>

<!-- sidebar -->
<aside class="abs side" style="top:766px">
  <div class="side-head"><svg width="18" height="18" viewBox="0 0 18 18"><circle cx="3" cy="15" r="2.2" fill="#fff"/><path d="M2 8a8 8 0 0 1 8 8M2 2a14 14 0 0 1 14 14" stroke="#fff" stroke-width="2.2" fill="none"/></svg>Search Blog</div>
  <div class="search-box"><div>Search...<svg width="14" height="14" viewBox="0 0 14 14"><circle cx="6" cy="6" r="4.2" stroke="#f8a21b" stroke-width="1.8" fill="none"/><path d="M9 9l4 4" stroke="#f8a21b" stroke-width="2"/></svg></div></div>
</aside>

<aside class="abs side" style="top:913px">
  <div class="tabs"><span class="on"><i></i>Friends</span><span><i></i>Updates</span><span><i></i>Photos</span></div>
  <div class="feed">
    <div class="item"><i class="ph2" role="img" aria-label="Follower avatar"></i><p>Lorem Ipsum is simply dummy text of the. printing and typesetting...<br><b>Like</b></p></div>
    <div class="item"><i class="ph6" role="img" aria-label="Follower avatar"></i><p>Lorem Ipsum is simply dummy text of the. printing and typesetting...<br><b>Like</b></p></div>
    <div class="item"><i class="ph5" role="img" aria-label="Follower avatar"></i><p>Lorem Ipsum is simply dummy text of the. printing and typesetting...<br><b>Like</b></p></div>
    <div class="item"><i class="ph6" role="img" aria-label="Follower avatar"></i><p>Lorem Ipsum is simply dummy text of the. printing and typesetting...<br><b>Like</b></p></div>
  </div>
</aside>

<aside class="abs side" style="top:1293px">
  <div class="side-head"><svg width="16" height="18" viewBox="0 0 16 18"><path d="M2 1h8l4 4v12H2z" stroke="#fff" stroke-width="1.8" fill="none"/><path d="M5 9h6M5 12h6" stroke="#fff" stroke-width="1.5"/></svg>Archives</div>
  <ul class="archive"><li>July 2016</li><li>June 2016</li><li>May 2016</li><li>April 2016</li><li>February 2016</li></ul>
</aside>

<aside class="abs side newsletter" style="top:1567px">
  <h5>SignUp For Newsletter</h5>
  <p>Lorem ipsum dolor sit amet, consecit</p>
  <div class="field">Enter your email address</div>
  <div class="btn">SUBMIT</div>
</aside>

<div class="abs promo-a" role="img" aria-label="Grey poster with a quote about education"></div>
<div class="abs promo-b" role="img" aria-label="Illustration of striped legs in red sneakers with a motivational slogan"></div>

<footer class="abs footer">Copyright © 2016 &nbsp;Tandem K &nbsp;| &nbsp;All Rights Reserved.</footer>
</body>
</html>
```